Brookmere Osteopathy flyer

I want a clean clear DL flyer (but also want an A4 poster) promoting a new Osteopathic business in a semi rural area in Tasmania (Australia).
It can have pictures like the examples attached to show people what Osteopathy is (its like Chiropractic and physiotherapy).
I am the sole practioner and am male, so any pictures would be best to be a white male if possible.
I've attached some wording, you can use all, or none of it
I don't have a phone number for the business yet
info@brookmereosteopathy.example
www.brookmereosteopathy.example
Target Market(s)
Australians, from tradies, professionals, babies to retired people
Industry/Entity Type
Health
Look and feel

```html
<!DOCTYPE html>
<html lang="en">
<head>
<meta charset="utf-8">
<title>Brookmere Osteopathy Flyer</title>
<link href="https://fonts.googleapis.com/css2?family=Poppins:wght@300;400;500;600;700;800&display=swap" rel="stylesheet">
<style>
  :root {
    --backdrop: #ebeaeb;
    --white: #ffffff;
    --orange: #f6913a;
    --sky: #0c98d3;
    --teal-navy: #075478;
    --navy: #062b43;
    --ink: #0d1620;
    --skin: #c9906e;
    --shadow-tone: #3a2c28;
    --divider: #c7d0d6;
  }
  * { box-sizing: border-box; margin: 0; padding: 0; }
  html, body { width: 1200px; height: 2202px; overflow: hidden; }
  body { background: var(--backdrop); font-family: "Poppins", sans-serif; position: relative; }

  .flyer {
    position: absolute; left: 154px; top: 154px; width: 892px; height: 1893px;
    background: var(--white); overflow: hidden;
    box-shadow: 0 6px 22px rgba(0,0,0,0.18);
  }

  .brand-mark {
    position: absolute; left: 88px; top: 92px; width: 278px; height: 278px;
    border: 2px solid var(--sky); border-radius: 50%;
    display: flex; align-items: center; justify-content: center; text-align: center;
  }
  .brand-name { color: var(--sky); font-weight: 600; font-size: 30px; line-height: 1.2; }

  .hero-band { position: absolute; left: 0; top: 402px; width: 100%; height: 459px; background: var(--orange); }

  .hero-photo {
    position: absolute; left: 400px; top: 49px; width: 674px; height: 674px;
    border-radius: 50%; border: 8px solid var(--white);
    background: radial-gradient(circle at 45% 55%, #d9a07d 0%, var(--skin) 35%, #6b4a3a 70%, var(--shadow-tone) 100%);
  }

  .headline { position: absolute; left: 85px; top: 440px; color: var(--white); }
  .headline .light { font-weight: 400; font-size: 62px; line-height: 62px; display: block; letter-spacing: 0.5px; }
  .headline .bold { font-weight: 700; font-size: 62px; line-height: 62px; display: block; }
  .headline .huge { font-weight: 800; font-size: 104px; line-height: 88px; display: block; color: var(--teal-navy); letter-spacing: -1px; }
  .headline .huge:first-of-type { margin-top: 6px; }

  .tagline {
    position: absolute; left: 86px; top: 764px; width: 700px;
    color: var(--white); font-weight: 700; font-size: 28px; line-height: 34px;
  }

  .reasons-title { position: absolute; left: 0; top: 893px; width: 100%; text-align: center; font-weight: 700; font-size: 39px; line-height: 42px; }
  .reasons-title .blue { color: var(--sky); display: block; }
  .reasons-title .orange { color: var(--orange); display: block; }
  .reasons-rule { position: absolute; left: 331px; top: 995px; width: 230px; height: 2px; background: var(--sky); }

  .reason-list { position: absolute; list-style: none; color: var(--ink); font-size: 25.5px; line-height: 30px; }
  .reason-list li { position: relative; padding-left: 35px; margin-bottom: 14px; }
  .reason-list li svg { position: absolute; left: 0; top: 4px; width: 25px; height: 25px; }
  .reasons-left { left: 88px; top: 1027px; width: 350px; }
  .reasons-right { left: 474px; top: 1022px; width: 400px; }
  .column-divider { position: absolute; left: 446px; top: 1017px; width: 1.5px; height: 258px; background: #9aa3aa; }

  .info-band { position: absolute; left: 0; top: 1400px; width: 100%; height: 297px; background: var(--sky); }
  .round-photo {
    position: absolute; top: 1303px; width: 228px; height: 228px; border-radius: 50%;
    border: 6px solid var(--white);
  }
  .round-photo.one { left: 83px; background: linear-gradient(140deg, #1f7fc4 0%, #c79274 45%, #e0b396 100%); }
  .round-photo.two { left: 330px; background: linear-gradient(180deg, #e9ecee 0%, #2c2f36 40%, #c28a68 70%, #27a59c 100%); }
  .round-photo.three { left: 580px; background: linear-gradient(180deg, #f2f2f2 0%, #d6a282 40%, #1e1e22 100%); }

  .about {
    position: absolute; left: 86px; top: 1555px; width: 720px;
    color: var(--white); font-size: 25.5px; line-height: 30.5px; font-weight: 400;
  }
  .about strong { font-weight: 700; }

  .contact-band { position: absolute; left: 0; top: 1697px; width: 100%; height: 196px; background: var(--navy); }
  .contact-list { position: absolute; left: 88px; top: 1740px; list-style: none; color: var(--white); font-size: 24px; line-height: 32px; }
  .contact-list li { position: relative; padding-left: 34px; }
  .contact-list svg, .address svg { position: absolute; left: 0; top: 5px; width: 23px; height: 23px; }
  .contact-divider { position: absolute; left: 602px; top: 1723px; width: 1.5px; height: 96px; background: var(--divider); }
  .address { position: absolute; left: 626px; top: 1724px; padding-left: 29px; color: var(--white); font-size: 24px; line-height: 30px; }
</style>
</head>
<body>
  <main class="flyer">
    <div class="brand-mark"><span class="brand-name">Brookmere<br>Osteopathy</span></div>

    <div class="hero-band"></div>
    <div class="hero-photo" role="img" aria-label="Photo of an osteopath's hands treating a patient's upper back and shoulder"></div>

    <h1 class="headline">
      <span class="light">NATURAL</span>
      <span class="bold">HEALING</span>
      <span class="huge">EXPERT</span>
      <span class="huge">HANDS</span>
    </h1>
    <p class="tagline">Treating the root cause of pain with gentle, effective osteopathic techniques.</p>

    <h2 class="reasons-title"><span class="blue">COMMON REASONS PEOPLE</span><span class="orange">VISIT AN OSTEOPATH</span></h2>
    <div class="reasons-rule"></div>

    <ul class="reason-list reasons-left">
      <li><svg viewBox="0 0 24 24"><circle cx="12" cy="12" r="11" fill="#0c98d3"/><path d="M7 12.5l3.2 3.2L17 9" stroke="#fff" stroke-width="2.6" fill="none" stroke-linecap="round" stroke-linejoin="round"/></svg>Back / neck pain</li>
      <li><svg viewBox="0 0 24 24"><circle cx="12" cy="12" r="11" fill="#0c98d3"/><path d="M7 12.5l3.2 3.2L17 9" stroke="#fff" stroke-width="2.6" fill="none" stroke-linecap="round" stroke-linejoin="round"/></svg>Headaches / migraines</li>
      <li><svg viewBox="0 0 24 24"><circle cx="12" cy="12" r="11" fill="#0c98d3"/><path d="M7 12.5l3.2 3.2L17 9" stroke="#fff" stroke-width="2.6" fill="none" stroke-linecap="round" stroke-linejoin="round"/></svg>Joint and muscle pain</li>
      <li><svg viewBox="0 0 24 24"><circle cx="12" cy="12" r="11" fill="#0c98d3"/><path d="M7 12.5l3.2 3.2L17 9" stroke="#fff" stroke-width="2.6" fill="none" stroke-linecap="round" stroke-linejoin="round"/></svg>Pregnancy-related<br>discomfort</li>
      <li><svg viewBox="0 0 24 24"><circle cx="12" cy="12" r="11" fill="#0c98d3"/><path d="M7 12.5l3.2 3.2L17 9" stroke="#fff" stroke-width="2.6" fill="none" stroke-linecap="round" stroke-linejoin="round"/></svg>Disc related issues</li>
    </ul>
    <div class="column-divider"></div>
    <ul class="reason-list reasons-right">
      <li><svg viewBox="0 0 24 24"><circle cx="12" cy="12" r="11" fill="#0c98d3"/><path d="M7 12.5l3.2 3.2L17 9" stroke="#fff" stroke-width="2.6" fill="none" stroke-linecap="round" stroke-linejoin="round"/></svg>Sciatica</li>
      <li><svg viewBox="0 0 24 24"><circle cx="12" cy="12" r="11" fill="#0c98d3"/><path d="M7 12.5l3.2 3.2L17 9" stroke="#fff" stroke-width="2.6" fill="none" stroke-linecap="round" stroke-linejoin="round"/></svg>Plantar fasciitis</li>
      <li><svg viewBox="0 0 24 24"><circle cx="12" cy="12" r="11" fill="#0c98d3"/><path d="M7 12.5l3.2 3.2L17 9" stroke="#fff" stroke-width="2.6" fill="none" stroke-linecap="round" stroke-linejoin="round"/></svg>Tendonitis / Bursitis</li>
      <li><svg viewBox="0 0 24 24"><circle cx="12" cy="12" r="11" fill="#0c98d3"/><path d="M7 12.5l3.2 3.2L17 9" stroke="#fff" stroke-width="2.6" fill="none" stroke-linecap="round" stroke-linejoin="round"/></svg>Adhesive capsulitis<br>(frozen shoulder)</li>
      <li><svg viewBox="0 0 24 24"><circle cx="12" cy="12" r="11" fill="#0c98d3"/><path d="M7 12.5l3.2 3.2L17 9" stroke="#fff" stroke-width="2.6" fill="none" stroke-linecap="round" stroke-linejoin="round"/></svg>Tennis / Golfers elbow</li>
    </ul>

    <div class="info-band"></div>
    <div class="round-photo one" role="img" aria-label="Photo of an osteopath applying deep tissue massage to a patient's back"></div>
    <div class="round-photo two" role="img" aria-label="Photo of a practitioner treating a patient lying face down on a treatment table"></div>
    <div class="round-photo three" role="img" aria-label="Photo of hands supporting the back of a patient's neck and shoulder"></div>

    <p class="about"><strong>Osteopaths</strong> use a combination of joint manipulation, targeted deep tissue massage and stretching to improve function, relieve pain and support the body’s ability to heal itself.</p>

    <div class="contact-band"></div>
    <ul class="contact-list">
      <li><svg viewBox="0 0 24 24"><circle cx="12" cy="12" r="12" fill="#f6913a"/><rect x="6.5" y="8" width="11" height="8" rx="1" fill="#fff"/><path d="M6.8 8.4l5.2 4 5.2-4" stroke="#f6913a" stroke-width="1.2" fill="none"/></svg>info@brookmereosteopathy.example</li>
      <li><svg viewBox="0 0 24 24"><circle cx="12" cy="12" r="12" fill="#f6913a"/><circle cx="12" cy="12" r="6" fill="none" stroke="#fff" stroke-width="1.5"/><path d="M6 12h12M12 6c-2.5 3.5-2.5 8.5 0 12M12 6c2.5 3.5 2.5 8.5 0 12" stroke="#fff" stroke-width="1.3" fill="none"/></svg>www.brookmereosteopathy.example</li>
    </ul>
    <div class="contact-divider"></div>
    <p class="address"><svg viewBox="0 0 24 24"><circle cx="12" cy="12" r="12" fill="#f6913a"/><path d="M12 5.5a4.2 4.2 0 0 0-4.2 4.2c0 3.2 4.2 7.8 4.2 7.8s4.2-4.6 4.2-7.8A4.2 4.2 0 0 0 12 5.5z" fill="#fff"/><circle cx="12" cy="9.7" r="1.6" fill="#f6913a"/></svg>48 Old<br>Mill road,<br>Brookmere</p>
  </main>
</body>
</html>
```